Brook Refrigeration. Refrigeration and air conditioning specialists.

We need a website to promote our business. We would a modern simple design using the colours from our logo and black. We want it to be fun but proffesional.

Target Market(s)

Commercial

Number of Pages Required

4 page

Requirements
Must have
• Home Page, About Us, Services and Contact Us.
• 24/7 365 days service available.
• Brook Refrigeration's dedicated team specialises in commercial refrigeration and air conditioning equipment.
• Based in Banksia Heights, we cover Harbour City Metro and surrounding areas.
Nice to have
• KNOWLEDGE . EXPERIENCE . PASSION in bold.
• Our experienced and highly trained technicians provide extensive knowledge and exceptional skills for your commercial refrigeration and air conditioning requirements.
• Pictures of commercial refrigeration.
Should not have
• No mention of domestic services.

```html
<!DOCTYPE html>
<html lang="en">
<head>
<meta charset="utf-8">
<title>Brook Refrigeration</title>
<link rel="stylesheet" href="https://fonts.googleapis.com/css2?family=Roboto:wght@400;500;700&family=Open+Sans:wght@400;600&display=swap">
<style>
:root{
  --lime:#8fd14f;
  --lime-dark:#77b83a;
  --purple:#3d2760;
  --purple-deep:#2a1947;
  --ink:#222;
  --text:#555;
  --muted:#888;
  --line:#ddd;
  --white:#fff;
}
*{box-sizing:border-box;margin:0;padding:0}
html,body{width:1200px;height:3432px;overflow:hidden}
body{font-family:"Open Sans",Arial,sans-serif;color:var(--text);background:var(--white);position:relative}
h1,h2,h3,.btn,.nav a{font-family:"Roboto",Arial,sans-serif}
.btn{display:inline-block;border-radius:30px;font-weight:500;font-size:14px;letter-spacing:1px;text-transform:uppercase;padding:12px 30px;text-decoration:none}
.btn-lime{background:var(--lime);color:var(--white)}
.btn-ghost{border:2px solid var(--white);color:var(--white)}

/* header */
.site-header{position:absolute;top:0;left:0;width:1200px;height:100px;background:var(--white);z-index:2}
.brand{position:absolute;left:40px;top:14px;display:flex;align-items:center;gap:12px}
.brand-mark{width:22px;height:22px;border-radius:50%;background:var(--lime)}
.brand-name{font-family:"Roboto",Arial,sans-serif;font-weight:700;font-size:30px;line-height:32px;color:var(--lime);width:220px}
.service-note{position:absolute;right:40px;top:22px;font-family:"Roboto",Arial,sans-serif;font-weight:700;font-size:15px;color:var(--ink);display:flex;align-items:center;gap:8px}
.nav{position:absolute;right:40px;top:60px;display:flex;gap:28px;align-items:center}
.nav a{font-size:13px;font-weight:700;color:var(--ink);text-decoration:none;text-transform:uppercase}
.nav a.active{color:var(--lime)}

/* hero */
.hero{position:absolute;top:100px;left:0;width:1200px;height:560px;background:linear-gradient(180deg,#4a5661 0%,#2e3a44 55%,#5d646b 100%);text-align:center}
.hero-photo{position:absolute;inset:0;background:radial-gradient(ellipse at 50% 60%,rgba(210,220,225,.35),rgba(0,0,0,0) 65%)}
.hero h1{position:relative;padding-top:160px;color:var(--white);font-size:62px;line-height:86px;font-weight:700;letter-spacing:3px}
.hero .btn{position:relative;margin-top:24px}
.dots{position:absolute;bottom:58px;left:0;width:100%;display:flex;justify-content:center;gap:8px}
.dots span{width:12px;height:12px;border-radius:50%;border:2px solid var(--white)}
.dots span.on{background:var(--white)}

/* welcome */
.welcome{position:absolute;top:660px;left:0;width:1200px;height:890px;text-align:center}
.welcome h2{margin-top:60px;font-size:34px;color:var(--purple);font-weight:700}
.rule{width:60px;height:3px;background:var(--lime);margin:18px auto 0}
.welcome .intro{width:900px;margin:24px auto 0;font-size:14px;line-height:24px}
.cards{position:absolute;top:252px;left:100px;display:flex;gap:40px}
.card{width:480px;height:548px;border:1px solid var(--line);background:var(--white)}
.card-photo{height:288px}
.card h3{margin-top:30px;font-size:26px;color:var(--ink);font-weight:500}
.card p{width:390px;height:63px;margin:16px auto 0;font-size:13px;line-height:21px;color:var(--muted)}
.card .btn{margin-top:40px;padding:10px 28px;font-size:12px}

/* why */
.why{position:absolute;top:1552px;left:0;width:1200px;height:528px;background:linear-gradient(100deg,var(--purple-deep) 0%,var(--purple) 55%,#5a4282 100%);color:var(--white)}
.why h2{position:absolute;left:160px;top:60px;font-size:32px;font-weight:700}
.why ul{position:absolute;left:160px;top:124px;width:420px;list-style:none}
.why li{display:flex;gap:12px;font-size:14px;line-height:22px;margin-bottom:20px}
.why li svg{flex:none;margin-top:4px}
.why .btn{position:absolute;left:160px;top:412px;padding:10px 26px}
.video{position:absolute;left:620px;top:96px;width:480px;height:400px;background:linear-gradient(135deg,#7a8a96,#2f3b45 60%,#c9d3d8)}
.play{position:absolute;left:210px;top:170px}

/* work */
.work{position:absolute;top:2080px;left:0;width:1200px;height:552px;text-align:center}
.work h2{margin-top:96px;font-size:32px;color:var(--ink);font-weight:700}
.work .rule{margin-top:14px}
.gallery{position:absolute;top:180px;left:100px;display:flex;gap:20px}
.shot{width:320px;height:260px;position:relative}
.shot figcaption{position:absolute;left:0;bottom:0;width:100%;padding:10px;background:rgba(255,255,255,.85);font-size:14px;font-weight:600;color:var(--ink);text-align:left}
.arrow{position:absolute;top:290px;width:40px;height:40px;border-radius:50%;border:1px solid #bbb;background:var(--white);display:flex;align-items:center;justify-content:center}

/* contact */
.contact{position:absolute;top:2632px;left:0;width:1200px;height:480px;background:linear-gradient(180deg,#9aa0a4,#6f767b 50%,#a7acaf);text-align:center}
.contact h2{margin-top:72px;font-size:32px;color:var(--white);font-weight:700;letter-spacing:1px}
.contact .rule{margin-top:14px}
.form{position:absolute;left:260px;top:150px;width:680px}
.row{display:flex;gap:16px;margin-bottom:12px}
.field{flex:1;height:36px;background:var(--white);font-size:12px;color:var(--muted);text-align:left;padding:10px 12px}
.field.message{height:72px}
.form .btn{margin-top:16px;padding:10px 44px}

/* footer */
.site-footer{position:absolute;top:3112px;left:0;width:1200px;height:320px;background:var(--white);text-align:center;font-size:12px;color:var(--text)}
.social{display:flex;justify-content:center;gap:14px;margin-top:84px}
.social span{width:38px;height:38px;border-radius:50%;border:1px solid #999}
.footer-contact{margin-top:44px;display:flex;justify-content:center;gap:18px}
.footer-links{margin-top:18px;display:flex;justify-content:center;gap:18px}
.copyright{margin-top:18px}
</style>
</head>
<body>

<header class="site-header">
  <div class="brand"><span class="brand-mark"></span><span class="brand-name">Brook Refrigeration</span></div>
  <div class="service-note">
    <svg width="16" height="16" viewBox="0 0 24 24"><path fill="#222" d="M6.6 10.8a15.1 15.1 0 0 0 6.6 6.6l2.2-2.2a1 1 0 0 1 1-.25 11.4 11.4 0 0 0 3.6.57 1 1 0 0 1 1 1V20a1 1 0 0 1-1 1A17 17 0 0 1 3 4a1 1 0 0 1 1-1h3.5a1 1 0 0 1 1 1c0 1.25.2 2.45.57 3.57a1 1 0 0 1-.25 1z"/></svg>
    24/7 365 DAYS SERVICE AVAILABLE
  </div>
  <nav class="nav">
    <a class="active" href="#">Home</a><a href="#">About Us</a><a href="#">Services</a><a href="#">Contact Us</a>
    <svg width="14" height="14" viewBox="0 0 24 24"><circle cx="10" cy="10" r="7" fill="none" stroke="#222" stroke-width="3"/><path d="M15 15l7 7" stroke="#222" stroke-width="3"/></svg>
  </nav>
</header>

<section class="hero">
  <div class="hero-photo" role="img" aria-label="Supermarket aisle lined with glass-door refrigerated display cabinets"></div>
  <h1>KNOWLEDGE .<br>EXPERIENCE . PASSION</h1>
  <a class="btn btn-ghost" href="#">Get More Info</a>
  <div class="dots"><span class="on"></span><span></span><span></span><span></span></div>
</section>

<section class="welcome">
  <h2>WELCOME TO BROOK REFRIGERATION</h2>
  <div class="rule"></div>
  <p class="intro">We keep cold rooms, display cases and cooling systems running for businesses across the region. Our friendly team delivers reliable repairs, installations and servicing, day or night.</p>
  <div class="cards">
    <article class="card">
      <div class="card-photo" role="img" aria-label="White commercial cool room with ceiling evaporator units" style="background:linear-gradient(160deg,#f2f3f4,#c9cdd0 60%,#e6e8ea)"></div>
      <h3>Commercial Refrigeration</h3>
      <p>Cool rooms, freezer rooms and display cabinets installed, serviced and repaired by qualified technicians who know the demands of busy kitchens and stores.</p>
      <a class="btn btn-lime" href="#">Read More</a>
    </article>
    <article class="card">
      <div class="card-photo" role="img" aria-label="Stainless steel commercial kitchen fridges and equipment" style="background:linear-gradient(160deg,#d9dcde,#9ea4a8 55%,#cfd3d5)"></div>
      <h3>Air Conditioning Equipment</h3>
      <p>Split systems, ducted units and packaged air conditioning supplied, fitted and maintained to keep offices, shops and warehouses comfortable all year.</p>
      <a class="btn btn-lime" href="#">Read More</a>
    </article>
  </div>
</section>

<section class="why">
  <h2>WHY CHOOSE US</h2>
  <ul>
    <li><svg width="14" height="14" viewBox="0 0 24 24"><path d="M3 12l6 6L21 5" fill="none" stroke="#8fd14f" stroke-width="4"/></svg>24/7 365 days service available.</li>
    <li><svg width="14" height="14" viewBox="0 0 24 24"><path d="M3 12l6 6L21 5" fill="none" stroke="#8fd14f" stroke-width="4"/></svg>Brook Refrigeration's dedicated team specialises in commercial refrigeration and air conditioning equipment.</li>
    <li><svg width="14" height="14" viewBox="0 0 24 24"><path d="M3 12l6 6L21 5" fill="none" stroke="#8fd14f" stroke-width="4"/></svg>Based in Banksia Heights, we cover Harbour City Metro and surrounding areas.</li>
    <li><svg width="14" height="14" viewBox="0 0 24 24"><path d="M3 12l6 6L21 5" fill="none" stroke="#8fd14f" stroke-width="4"/></svg>Our experienced and highly trained technicians provide extensive knowledge and exceptional skills for your commercial refrigeration and air conditioning requirements.</li>
  </ul>
  <a class="btn btn-ghost" href="#">Read More</a>
  <div class="video" role="img" aria-label="Video still of a technician working on a refrigerated display cabinet">
    <svg class="play" width="60" height="60" viewBox="0 0 60 60"><circle cx="30" cy="30" r="30" fill="#111"/><path d="M24 18l18 12-18 12z" fill="#fff"/></svg>
  </div>
</section>

<section class="work">
  <h2>OUR WORK</h2>
  <div class="rule"></div>
  <div class="gallery">
    <figure class="shot" role="img" aria-label="Stainless steel refrigeration units in a production facility" style="background:linear-gradient(160deg,#c6cbcf,#7f878d 60%,#b4babe)"></figure>
    <figure class="shot" role="img" aria-label="Row of supermarket display cases stocked with drinks" style="background:linear-gradient(160deg,#8fc3e0,#2f6fa0 55%,#9ccde6)"><figcaption>Supermarket Display Cases</figcaption></figure>
    <figure class="shot" role="img" aria-label="Open cool room door with insulated panels" style="background:linear-gradient(160deg,#e8eaeb,#9aa0a4 60%,#d4d7d9)"></figure>
  </div>
  <div class="arrow" style="left:28px"><svg width="12" height="12" viewBox="0 0 12 12"><path d="M8 1L3 6l5 5" fill="none" stroke="#666" stroke-width="2"/></svg></div>
  <div class="arrow" style="left:1132px"><svg width="12" height="12" viewBox="0 0 12 12"><path d="M4 1l5 5-5 5" fill="none" stroke="#666" stroke-width="2"/></svg></div>
</section>

<section class="contact" role="img" aria-label="Background of silver air conditioning ducting">
  <h2>GET IN TOUCH</h2>
  <div class="rule"></div>
  <div class="form">
    <div class="row"><div class="field">First Name</div><div class="field">Last Name</div></div>
    <div class="row"><div class="field">Email Address</div><div class="field">Phone Number</div></div>
    <div class="row"><div class="field message">Message</div></div>
    <a class="btn btn-lime" href="#">Submit</a>
  </div>
</section>

<footer class="site-footer">
  <div class="social"><span></span><span></span><span></span><span></span></div>
  <div class="footer-contact">
    <span>18 Wattle Grove Rd, Banksia Heights 7042</span>
    <span>1 800 555 0142</span>
    <span>info@brookrefrigeration.example</span>
  </div>
  <div class="footer-links"><span>Help</span><span>FAQ</span><span>Support</span><span>Sitemap</span><span>Terms Of Use</span><span>Privacy Statement</span></div>
  <p class="copyright">Brook Refrigeration. © 2018 All rights reserved.</p>
</footer>

</body>
</html>
```